Orvel CCTV A5 Flyer for attracting sales

Looking for an A5 flyer to be designed to advertise 3 specific CCTV packages from my website www.orvelcctv-example.com. the packages are I - 3 camera solution J - 4 cameras and L - 5 cameras. The background of the flyer should be white as I will be printing these myself on standard white A5 paper. Need to advertise also the business contact details and for it to say somewhere "protect your home with our CCTV packages". Also need to get the message across that we supply and install as well as there being a 1 year onsite warranty with all our packages. If you feel A5 is not big enough then feel free to design on A4

```html
<!DOCTYPE html>
<html lang="en">
<head>
<meta charset="utf-8">
<title>Orvel CCTV Ltd – CCTV Packages Flyer</title>
<link rel="stylesheet" href="https://fonts.googleapis.com/css2?family=Anton&family=Roboto+Condensed:wght@300;400;700&family=Open+Sans:wght@400;600;700&family=Arimo:wght@400;700&display=swap">
<style>
  :root {
    --orange: #f18a32;
    --yellow: #fbd31d;
    --ink: #2b2b2b;
    --grey: #d4d5d7;
    --blue: #1f5aa6;
    --blue-dark: #163f80;
    --sky: #4aa3ea;
    --white: #ffffff;
    --red: #d7262e;
  }
  * { box-sizing: border-box; margin: 0; padding: 0; }
  html, body { width: 849px; height: 1200px; overflow: hidden; background: var(--white); }
  .flyer { position: relative; width: 849px; height: 1200px; overflow: hidden; background: var(--white); font-family: "Open Sans", sans-serif; }
  .backdrop { position: absolute; inset: 0; }

  .brand { position: absolute; top: 78px; left: 0; width: 849px; display: flex; align-items: center; justify-content: center; gap: 22px; }
  .brand-dot { width: 86px; height: 86px; border-radius: 50%; background: var(--ink); }
  .brand-name { font-family: "Anton", sans-serif; font-size: 64px; color: var(--ink); letter-spacing: 0.5px; }

  .tagline { position: absolute; top: 218px; width: 849px; text-align: center; font-family: "Roboto Condensed", sans-serif; font-weight: 400; font-size: 39px; color: var(--ink); }

  .offer-panel { position: absolute; left: 64px; top: 291px; width: 717px; height: 250px; background: var(--orange); border-radius: 42px 42px 0 0; }
  .offer-copy { position: absolute; top: 326px; width: 849px; text-align: center; font-family: "Roboto Condensed", sans-serif; font-weight: 300; font-size: 35px; line-height: 48px; color: var(--white); }
  .offer-copy strong { font-weight: 700; }
  .packages-title { position: absolute; top: 443px; width: 849px; text-align: center; font-family: "Anton", sans-serif; font-size: 50px; color: var(--white); text-shadow: 2px 4px 4px rgba(120,50,0,0.45); }

  .package { position: absolute; top: 530px; width: 208px; height: 490px; background: var(--white); border-radius: 0 0 104px 104px; overflow: hidden; box-shadow: 10px 12px 18px rgba(0,0,0,0.18); text-align: center; }
  .package.i { left: 64px; } .package.j { left: 318px; } .package.l { left: 573px; }
  .package-head { height: 187px; background: var(--orange); padding-top: 28px; }
  .package-code { font-family: "Anton", sans-serif; font-size: 72px; line-height: 80px; color: var(--yellow); text-shadow: 3px 3px 0 rgba(60,40,0,0.55); }
  .package-label { font-family: "Open Sans", sans-serif; font-weight: 600; font-size: 29px; line-height: 31px; color: var(--white); }
  .maker { display: flex; justify-content: center; align-items: center; gap: 18px; margin-top: 20px; }
  .maker-name { font-family: "Arimo", sans-serif; font-weight: 700; font-size: 15px; color: var(--red); letter-spacing: 1px; }
  .hd-badge { width: 34px; height: 30px; background: var(--yellow); border-radius: 3px; }
  .cameras { height: 36px; margin: 8px auto 0; width: 180px; border-radius: 18px; background: linear-gradient(#ffffff, #d9dadc); }
  .recorder { height: 30px; margin: 8px auto 0; width: 178px; border-radius: 2px; background: linear-gradient(#3a3b3d, #1d1e20); }
  .package-name { margin-top: 16px; font-family: "Arimo", sans-serif; font-size: 18.5px; line-height: 22px; color: var(--ink); }
  .package-name b { display: block; font-weight: 700; }
  .sku { font-family: "Arimo", sans-serif; font-size: 16px; color: #666; line-height: 20px; }
  .price { margin-top: 17px; font-family: "Arimo", sans-serif; font-weight: 700; font-size: 16px; color: var(--ink); }

  .contacts { position: absolute; left: 56px; top: 1055px; color: var(--white); font-size: 17px; font-style: normal; }
  .contact-row { display: flex; align-items: center; gap: 12px; height: 38px; }
  .contact-row svg { width: 20px; height: 20px; flex: none; }
  .contact-row .gap { width: 18px; }
  .contact-row b { font-weight: 700; }

  .promo { position: absolute; right: 24px; top: 1100px; text-align: right; font-family: "Arimo", sans-serif; color: var(--ink); }
  .promo-get { font-family: "Roboto Condensed", sans-serif; font-size: 22px; line-height: 22px; color: var(--yellow); }
  .promo-amount { font-family: "Roboto Condensed", sans-serif; font-weight: 700; font-size: 32px; line-height: 32px; color: var(--yellow); }
  .promo-small { font-size: 8.5px; line-height: 10px; font-weight: 700; }
  .promo-code { font-size: 9.5px; line-height: 11px; }
  .promo-code span { color: var(--yellow); font-weight: 700; }
</style>
</head>
<body>
<div class="flyer">
  <svg class="backdrop" width="849" height="1200" viewBox="0 0 849 1200">
    <path d="M0 475 Q120 500 200 540 L650 540 Q740 500 849 470 L849 1200 L0 1200 Z" fill="var(--grey)"/>
    <path d="M0 818 Q300 900 560 900 Q720 900 849 870 L849 1200 L0 1200 Z" fill="var(--blue)"/>
    <path d="M0 1000 Q400 1100 849 1040 L849 1200 L0 1200 Z" fill="var(--blue-dark)" opacity="0.5"/>
    <path d="M620 1076 Q760 1060 849 1010 L849 1200 L570 1200 Q610 1150 620 1076 Z" fill="var(--orange)"/>
    <path d="M620 1076 Q700 1068 760 1050 Q700 1090 690 1200 L570 1200 Q610 1150 620 1076 Z" fill="#3d8fe0"/>
    <path d="M660 1096 Q760 1080 849 1030 L849 1200 L650 1200 Q670 1150 660 1096 Z" fill="var(--white)"/>
  </svg>

  <div class="brand"><span class="brand-dot"></span><span class="brand-name">Orvel CCTV Ltd</span></div>
  <h1 class="tagline">Protect your home with our CCTV packages</h1>

  <div class="offer-panel"></div>
  <p class="offer-copy">we supply and install as well as there being a<br><strong>1 year onsite warranty</strong> with all our packages</p>
  <h2 class="packages-title">Our 3 specific CCTV packages</h2>

  <article class="package i">
    <div class="package-head"><div class="package-code">I-3</div><div class="package-label">Camera<br>Solution</div></div>
    <div class="maker"><span class="maker-name">VARNIK</span><span class="hd-badge"></span></div>
    <div class="cameras" role="img" aria-label="Three white dome cameras"></div>
    <div class="recorder" role="img" aria-label="Video recorder unit"></div>
    <p class="package-name">(Home Kit I 1080)<b>3 camera<br>CCTV Package<br>Installation</b></p>
    <p class="sku">SKU: OC-103</p>
    <p class="price">£ 609.95</p>
  </article>

  <article class="package j">
    <div class="package-head"><div class="package-code">J-4</div><div class="package-label">Cameras<br>Solution</div></div>
    <div class="maker"><span class="maker-name">VARNIK</span><span class="hd-badge"></span></div>
    <div class="cameras" role="img" aria-label="Four white dome cameras"></div>
    <div class="recorder" role="img" aria-label="Video recorder unit"></div>
    <p class="package-name">(Home Kit J 1080)<b>4 camera<br>CCTV Package<br>Installation</b></p>
    <p class="sku">SKU: OC-104</p>
    <p class="price">£ 659.95</p>
  </article>

  <article class="package l">
    <div class="package-head"><div class="package-code">L-5</div><div class="package-label">Cameras<br>Solution</div></div>
    <div class="maker"><span class="maker-name">VARNIK</span><span class="hd-badge"></span></div>
    <div class="cameras" role="img" aria-label="Five white dome cameras"></div>
    <div class="recorder" role="img" aria-label="Video recorder unit"></div>
    <p class="package-name">(Home Kit L 1080)<b>5 camera<br>CCTV Package<br>Installation</b></p>
    <p class="sku">SKU: OC-105</p>
    <p class="price">£ 759.95</p>
  </article>

  <address class="contacts">
    <div class="contact-row">
      <svg viewBox="0 0 20 20"><path d="M10 1a6 6 0 0 0-6 6c0 5 6 12 6 12s6-7 6-12a6 6 0 0 0-6-6z" fill="var(--sky)"/><circle cx="10" cy="7" r="2.2" fill="var(--blue)"/></svg>
      <span><b>Orvel CCTV Ltd</b> 14 Harlow Street, London N2 4QX</span>
    </div>
    <div class="contact-row">
      <svg viewBox="0 0 20 20"><path d="M5 2l3 4-2 2c1 2 3 4 5 5l2-2 4 3-2 3C8 17 3 12 2 5z" fill="var(--sky)"/></svg>
      <span>020 7946 0381</span><span class="gap"></span>
      <svg viewBox="0 0 20 20"><rect x="1" y="4" width="18" height="12" fill="var(--sky)"/><path d="M1 4l9 7 9-7" stroke="var(--blue)" stroke-width="1.5" fill="none"/></svg>
      <span>info@orvelcctv-example.com</span>
    </div>
    <div class="contact-row">
      <svg viewBox="0 0 20 20"><rect x="5" y="1" width="10" height="18" rx="2" fill="var(--sky)"/><rect x="7" y="4" width="6" height="10" fill="var(--blue)"/></svg>
      <span>07700 900 214</span><span class="gap"></span>
      <svg viewBox="0 0 20 20"><circle cx="10" cy="10" r="8" fill="none" stroke="var(--sky)" stroke-width="1.6"/><ellipse cx="10" cy="10" rx="3.5" ry="8" fill="none" stroke="var(--sky)" stroke-width="1.4"/><path d="M2 10h16" stroke="var(--sky)" stroke-width="1.4"/></svg>
      <span>www.orvelcctv-example.com</span>
    </div>
  </address>

  <aside class="promo">
    <div class="promo-get">Get</div>
    <div class="promo-amount">£25 off</div>
    <div class="promo-small">our best-selling 4 Camera<br>CCTV Package in January 2018.</div>
    <div class="promo-code">Use the code <span>ORV25</span> at the checkout</div>
  </aside>
</div>
</body>
</html>
```